We need a business card for our gym. We are a PowerCore affiliate in Decatur Georgie established 2008. Our company name is Rally Functional Fitness. PowerCore Building Prime Fitness. Instagram and website is @rallygym. Hashtags we use #rallywithheart #madetorally We want something similar to the the black and neon green design attached but a different color scheme. No neon colors. Are company colors are the same as the blue and white card attached. We are open to ideas as far as colors however - just no neon.

Contact Information for Business Card

Rally Functional Fitness
472 Halvern Drive
Decatur GA 30041
Phone 404.555.0187 Website www.rallygym.example

Font styles to use
Other font styles liked:
• Futura Extra Bold Condensed

Colors

Designer to choose colors to be used in the design.

Requirements
Must have
• Our primary font we typically use for our name is Futura Extra Bold Condensed
Nice to have
• I attached a card from that is black and neon green from Zorva that we would like something similar. The blue and white is more similar to our colors. We also use have used black and white in the past. We use the chevrons as out logo. We are a PowerCore affiliate so I included a logo from them as well that may or may not be used on the card. Our instagram is @rallygym hashtags #madetorally #rallywithheart
Should not have
• No neon colors

```html
<!DOCTYPE html>
<html lang="en">
<head>
<meta charset="utf-8">
<title>Rally Functional Fitness — Business Card</title>
<link rel="stylesheet" href="https://fonts.googleapis.com/css2?family=Oswald:wght@700&family=Montserrat:wght@500&display=swap">
<style>
  :root {
    --backdrop: #2b2b2c;
    --card: #1b1b1c;
    --card-edge: #101011;
    --ink-brand: #4a4c4a;
    --ink-name: #4a4b4a;
    --ink-title: #3f403f;
    --ink-contact: #8c8d8c;
    --ink-address: #5e5f5e;
    --rule: #4a4b4a;
  }
  * { margin: 0; padding: 0; box-sizing: border-box; }
  html, body {
    width: 1200px; height: 901px; overflow: hidden;
    background: var(--backdrop);
  }
  .sheet {
    width: 1200px; height: 901px;
    display: flex; flex-direction: column;
    align-items: center; justify-content: center; gap: 44px;
  }
  .card {
    width: 630px; height: 360px;
    background: var(--card);
    border-bottom: 4px solid var(--card-edge);
    position: relative;
  }
  /* Front */
  .card--front {
    display: flex; align-items: center; justify-content: center;
  }
  .brand-name {
    font-family: "Oswald", sans-serif;
    font-weight: 700;
    font-size: 44px;
    letter-spacing: 2px;
    color: var(--ink-brand);
    text-transform: uppercase;
    white-space: nowrap;
    line-height: 1;
  }

  /* Back */
  .card--back { padding: 0 40px; }
  .identity-row {
    position: absolute; left: 0; right: 0; top: 108px;
    display: flex; justify-content: center; align-items: stretch;
  }
  .identity {
    text-align: right; padding-right: 22px;
    border-right: 1px solid var(--rule);
  }
  .identity__name {
    font-family: "Oswald", sans-serif; font-weight: 700;
    font-size: 31px; letter-spacing: 0.5px;
    color: var(--ink-name); text-transform: uppercase; line-height: 1.1;
  }
  .identity__title {
    font-family: "Montserrat", sans-serif; font-weight: 500;
    font-size: 19px; color: var(--ink-title);
    text-transform: uppercase; letter-spacing: 0.5px; margin-top: 2px;
  }
  .contacts {
    list-style: none; padding-left: 22px;
    font-family: "Montserrat", sans-serif; font-weight: 500;
    font-size: 18px; color: var(--ink-contact);
  }
  .contacts li { display: flex; align-items: center; gap: 8px; line-height: 1.45; }
  .contacts svg { width: 15px; height: 15px; fill: var(--ink-contact); flex: none; }
  .address {
    position: absolute; left: 0; right: 0; bottom: 52px;
    text-align: center;
    font-family: "Montserrat", sans-serif; font-weight: 500;
    font-size: 20px; color: var(--ink-address);
  }
</style>
</head>
<body>
<main class="sheet">
  <section class="card card--front" aria-label="Card front">
    <h1 class="brand-name">Rally Functional Fitness</h1>
  </section>

  <section class="card card--back" aria-label="Card back">
    <div class="identity-row">
      <div class="identity">
        <p class="identity__name">Marcus Tellford</p>
        <p class="identity__title">Expert Coaches</p>
      </div>
      <ul class="contacts">
        <li>
          <svg viewBox="0 0 24 24" aria-hidden="true"><path d="M6.6 10.8a15.1 15.1 0 0 0 6.6 6.6l2.2-2.2a1 1 0 0 1 1-.25 11.4 11.4 0 0 0 3.6.57 1 1 0 0 1 1 1V20a1 1 0 0 1-1 1A17 17 0 0 1 3 4a1 1 0 0 1 1-1h3.5a1 1 0 0 1 1 1c0 1.25.2 2.45.57 3.57a1 1 0 0 1-.25 1z"/></svg>
          404.555.0187
        </li>
        <li>
          <svg viewBox="0 0 24 24" aria-hidden="true"><path d="M2 5h20v14H2zm2 2v.4l8 5.1 8-5.1V7zm0 2.8V17h16V9.8l-8 5.1z"/></svg>
          info@rallygym.example
        </li>
        <li>
          <svg viewBox="0 0 24 24" aria-hidden="true"><path d="M12 2a10 10 0 1 0 0 20 10 10 0 0 0 0-20zm0 2c.9 0 2.2 2 2.7 5H9.3C9.8 6 11.1 4 12 4zM4.3 10h3a16 16 0 0 0 0 4h-3a8 8 0 0 1 0-4zm5 0h5.4a14 14 0 0 1 0 4H9.3a14 14 0 0 1 0-4zm7.4 0h3a8 8 0 0 1 0 4h-3a16 16 0 0 0 0-4zM9.3 15h5.4c-.5 3-1.8 5-2.7 5s-2.2-2-2.7-5z"/></svg>
          www.rallygym.example
        </li>
      </ul>
    </div>
    <p class="address">472 Halvern Drive, Decatur GA 30041</p>
  </section>
</main>
</body>
</html>
```